New Business Card Design for Manufacturing

We are an engineering/manufacturing company that offers Advanced machining/assembly/engineering services, as well as innovative products for the heavy duty engine cooling markets.

We are looking to get a new business card designed that is clean and modern looking, but still fits the wide range of technical/skilled work we do.

- We hope to use this design as the base for other design work in new Presentations, web, and print work.

Industry/Entity Type

Engineering

Contact Information for Business Card

Our preferred color of blue is (RGB) 22/71/159 but can vary slightly from that color. Our content will be our Logo and full company name (Vantrell Forge Works, Inc.), company address, name, job title, phone number with extension, cell number, fax number, website, and email address on the cards.
We'd like the full company name next to the logo, but we are open to other interpretations of that layout.
Preferably, we would like the back side to be clean with just our logo, and the front to contain all of the contact information.

Colors
2f74b4
0355a3
85abd2

Requirements
Must have
• - Logo, company name, needed content - We are open to interpretation beyond that.
• - Standard size business card.
• - Horizontal orientation.
• - Enough space for lengthy names / job titles (for example, a job title could read "Directory of Human Resources" or "V.P. of Governmental Affairs"). We need this to look clean, whether the title be short (CEO) or long (as described above).

```html
<!DOCTYPE html>
<html lang="en">
<head>
<meta charset="utf-8">
<title>Vantrell Forge Works – Business Card</title>
<link href="https://fonts.googleapis.com/css2?family=Oswald:wght@500&family=Work+Sans:wght@300;400;700&display=swap" rel="stylesheet">
<style>
  :root {
    --brand-blue: #16479f;
    --brand-blue-bright: #0355a3;
    --ink-grey: #8a8a8a;
    --card-white: #ffffff;
    --card-black: #000000;
    --backdrop: #d2d2d2;
  }
  html, body {
    margin: 0;
    width: 1200px;
    height: 800px;
    overflow: hidden;
    background: var(--backdrop);
  }
  .canvas {
    position: relative;
    width: 1200px;
    height: 800px;
  }
  .card {
    position: absolute;
    top: 245px;
    width: 540px;
    height: 309px;
    box-shadow: 0 4px 14px rgba(0,0,0,0.18);
    overflow: hidden;
  }
  .card--front { left: 40px; background: var(--card-white); }
  .card--back  { left: 620px; background: var(--card-black); }

  /* Front */
  .person {
    position: absolute;
    left: 32px;
    top: 134px;
    width: 254px;
  }
  .person__name {
    font-family: "Oswald", sans-serif;
    font-weight: 500;
    font-size: 28px;
    letter-spacing: 1.5px;
    line-height: 1;
    color: var(--brand-blue);
    margin: 0;
    white-space: nowrap;
  }
  .person__title {
    font-family: "Work Sans", sans-serif;
    font-weight: 300;
    font-size: 14px;
    color: var(--ink-grey);
    margin: 5px 0 0;
    white-space: nowrap;
  }
  .divider {
    position: absolute;
    left: 304px;
    top: 94px;
    width: 1.5px;
    height: 120px;
    background: var(--brand-blue-bright);
  }
  .contact {
    position: absolute;
    left: 322px;
    top: 98px;
    font-family: "Work Sans", sans-serif;
    font-weight: 300;
    font-size: 13px;
    line-height: 19px;
    color: var(--ink-grey);
    margin: 0;
    padding: 0;
    list-style: none;
  }
  .contact__row { display: flex; align-items: center; gap: 6px; white-space: nowrap; }
  .contact__icon { width: 10px; height: 10px; flex: none; }
  .contact__row--plain { padding-left: 16px; }
  .domain { color: var(--brand-blue-bright); font-weight: 400; }

  /* Back */
  .brand {
    position: absolute;
    left: 70px;
    top: 118px;
    display: flex;
    align-items: center;
    gap: 14px;
  }
  .brand__mark {
    width: 34px;
    height: 34px;
    background: var(--brand-blue-bright);
  }
  .brand__name {
    font-family: "Work Sans", sans-serif;
    font-weight: 700;
    font-size: 25px;
    line-height: 1.1;
    color: var(--brand-blue-bright);
    text-transform: uppercase;
    margin: 0;
  }
  .back-web {
    position: absolute;
    right: 32px;
    bottom: 26px;
    font-family: "Work Sans", sans-serif;
    font-weight: 300;
    font-size: 17px;
    color: #ffffff;
    margin: 0;
  }
</style>
</head>
<body>
<main class="canvas">
  <section class="card card--front" aria-label="Business card front">
    <div class="person">
      <h1 class="person__name">MARISA DELCOURT</h1>
      <p class="person__title">Directory of Human Resources</p>
    </div>
    <div class="divider"></div>
    <ul class="contact">
      <li class="contact__row contact__row--plain">418 Corwin Ave., Ste. 210</li>
      <li class="contact__row contact__row--plain">Fort Wayne, IN 46802 USA</li>
      <li class="contact__row">
        <svg class="contact__icon" viewBox="0 0 10 10" aria-hidden="true"><path d="M2 1 L4 1 L4.6 3 L3.5 4 Q4.5 6 6 6.5 L7 5.4 L9 6 L9 8 Q5 9 2 6 Q0.8 3.5 2 1Z" fill="#16479f"/></svg>
        (260) 555-0148
      </li>
      <li class="contact__row">
        <svg class="contact__icon" viewBox="0 0 10 10" aria-hidden="true"><rect x="0.8" y="2" width="8.4" height="6" fill="none" stroke="#16479f" stroke-width="1.2"/><path d="M1 2.3 L5 5.5 L9 2.3" fill="none" stroke="#16479f" stroke-width="1.2"/></svg>
        info@vantrellforge.com
      </li>
      <li class="contact__row">
        <svg class="contact__icon" viewBox="0 0 10 10" aria-hidden="true"><circle cx="5" cy="5" r="4.2" fill="none" stroke="#16479f" stroke-width="1.1"/><ellipse cx="5" cy="5" rx="1.8" ry="4.2" fill="none" stroke="#16479f" stroke-width="1"/><path d="M0.8 5 H9.2" stroke="#16479f" stroke-width="1"/></svg>
        <span>www.<span class="domain">vantrellforge</span>.com</span>
      </li>
    </ul>
  </section>

  <section class="card card--back" aria-label="Business card back">
    <div class="brand">
      <div class="brand__mark"></div>
      <p class="brand__name">Vantrell Forge<br>Works, Inc.</p>
    </div>
    <p class="back-web">www.<span class="domain">vantrellforge</span>.com</p>
  </section>
</main>
</body>
</html>
```